Telecommunications Company needs a business card design

We are looking for a sleek, professional and modern business card design based off our new logo. Will look at both light and dark options. On some designs please provide a small space for a QR code

Target Market(s)

B2B clients in Australia

Contact Information for Business Card

Name, Position, Brisbane (head) office, Phone number, email address, QR code (link to our website qlinetelecom.com.au

Colors
0054AA
0677BA
7BADD7
CADEEF
E8F1F8
0094D4
00A9DD
6FCCEA
C7EBF8
E9F6FB
00AB8E
00BBA5
67D7C9
C6EFE9
E9F9F6

```html
<!DOCTYPE html>
<html lang="en">
<head>
<meta charset="utf-8">
<title>Qline Telecom – Business Card</title>
<link href="https://fonts.googleapis.com/css2?family=Montserrat:wght@400;500;700&display=swap" rel="stylesheet">
<style>
  :root {
    --backdrop: #d6d6d6;
    --card-light: #ffffff;
    --card-dark: #1a1b1d;
    --card-dark-edge: #121314;
    --brand-blue: #0677BA;
    --brand-deep: #0054AA;
    --brand-teal: #00A9DD;
    --ink: #1d1d1f;
    --pattern-tone: #2b2c2f;
  }
  * { margin: 0; padding: 0; box-sizing: border-box; }
  html, body { width: 1200px; height: 965px; overflow: hidden; }
  body {
    background: var(--backdrop);
    font-family: "Montserrat", sans-serif;
    position: relative;
  }
  .card {
    position: absolute;
    top: 114px;
    width: 421px;
    height: 736px;
  }
  .card--front { left: 141px; background: var(--card-light); color: var(--ink); }
  .card--back { left: 638px; background: var(--card-dark); overflow: hidden; }

  .brand-name {
    position: absolute;
    left: 0; right: 0;
    top: 52px;
    text-align: center;
    color: var(--brand-blue);
    font-weight: 700;
    line-height: 1;
  }
  .brand-name__main { display: block; font-size: 110px; letter-spacing: 2px; }
  .brand-name__sub { display: block; font-size: 37px; letter-spacing: 3px; margin-top: 18px; }

  .person {
    position: absolute;
    left: 0; right: 0;
    top: 445px;
    text-align: center;
  }
  .person__name { font-size: 29px; font-weight: 700; color: var(--brand-blue); line-height: 1; }
  .person__role { font-size: 19px; font-weight: 400; margin-top: 5px; line-height: 1; }

  .contact-rule { position: absolute; left: 50px; top: 520px; }

  .contact-list {
    position: absolute;
    left: 0; right: 0;
    top: 562px;
    text-align: center;
    list-style: none;
    font-size: 19px;
    line-height: 26px;
  }
  .divider {
    position: absolute;
    left: 50px;
    top: 655px;
    width: 321px;
    height: 2px;
    background: var(--brand-blue);
  }
  .office {
    position: absolute;
    left: 0; right: 0;
    top: 678px;
    text-align: center;
    font-size: 19px;
  }

  .back-pattern {
    position: absolute;
    inset: 0;
    background: linear-gradient(160deg, #2a2b2e 0%, var(--pattern-tone) 30%, var(--card-dark) 65%, var(--card-dark-edge) 100%);
  }
  .back-mark {
    position: absolute;
    left: 256px;
    top: 638px;
    font-size: 31px;
    font-weight: 700;
    color: var(--brand-teal);
    letter-spacing: 1px;
    line-height: 1;
  }
</style>
</head>
<body>
  <section class="card card--front" aria-label="Business card front">
    <div class="brand-name">
      <span class="brand-name__main">QLINE</span>
      <span class="brand-name__sub">TELECOM</span>
    </div>

    <div class="person">
      <p class="person__name">MARK ELLISON</p>
      <p class="person__role">Director</p>
    </div>

    <svg class="contact-rule" width="321" height="26" viewBox="0 0 321 26" aria-hidden="true">
      <line x1="0" y1="13" x2="107" y2="13" stroke="#0677BA" stroke-width="1.5"/>
      <line x1="215" y1="13" x2="321" y2="13" stroke="#0677BA" stroke-width="1.5"/>
      <g transform="translate(130 13)">
        <circle r="12" fill="#0677BA"/>
        <path d="M-4.5 -6 l2.5 -1 l2 4 l-1.8 1.3 q1.2 3 3.6 4.6 l1.5 -1.6 l3.6 2.4 l-1 2.4 q-5 1 -8.6 -4.6 q-3 -4.5 -1.8 -7.5z" fill="#fff"/>
      </g>
      <g transform="translate(160 13)">
        <circle r="12" fill="#0677BA"/>
        <rect x="-6.5" y="-4.5" width="13" height="9" rx="1.2" fill="none" stroke="#fff" stroke-width="1.4"/>
        <path d="M-6 -3.8 L0 1 L6 -3.8" fill="none" stroke="#fff" stroke-width="1.4"/>
      </g>
      <g transform="translate(191 13)" fill="none" stroke="#fff" stroke-width="1.2">
        <circle r="12" fill="#0677BA" stroke="none"/>
        <circle r="6.5"/>
        <ellipse rx="2.8" ry="6.5"/>
        <line x1="-6.5" y1="0" x2="6.5" y2="0"/>
        <line x1="-5.6" y1="-3.3" x2="5.6" y2="-3.3"/>
        <line x1="-5.6" y1="3.3" x2="5.6" y2="3.3"/>
      </g>
    </svg>

    <ul class="contact-list">
      <li>(123) 456-7890</li>
      <li>qlinetelecom.com.au</li>
      <li>qlinetelecom.com.au</li>
    </ul>

    <div class="divider"></div>
    <p class="office">Brisbane (head) office</p>
  </section>

  <section class="card card--back" aria-label="Business card back">
    <div class="back-pattern" role="img" aria-label="Tone-on-tone repeating brand pattern across a dark background"></div>
    <span class="back-mark">QLINE</span>
  </section>
</body>
</html>
```